New LLC consulting company needs a business card design

I need a business card design for new company in Alexandria Virginia called TK Verdane Consulting LLC. The company is focused on consulting for defense and national security issues with expertise in nuclear and space topics. I would like to see designs that are simple and I am open to colors except for brown.

Target Market(s)

All businesses that are seeking consulting help

Industry/Entity Type

Consulting

Contact Information for Business Card

Name of company - TK Verdane Consulting LLC; name (Delia Pratt) President; email: prattdq47@mailvessa.com; Phone: 703-555-0142

Requirements
Must have
• The details described above
Nice to have
• I'm open to all ideas
Should not have
• No brown

```html
<!DOCTYPE html>
<html lang="en">
<head>
<meta charset="utf-8">
<title>Delia Pratt — TK Verdane Consulting LLC</title>
<link rel="stylesheet" href="https://fonts.googleapis.com/css2?family=Montserrat:wght@400;600&display=swap">
<style>
  :root {
    --backdrop: #1e1e1e;
    --card: #ffffff;
    --ink: #000000;
    --ink-soft: #222222;
  }
  html, body {
    margin: 0;
    padding: 0;
    width: 1200px;
    height: 1059px;
    overflow: hidden;
    background: var(--backdrop);
  }
  .canvas {
    position: relative;
    width: 1200px;
    height: 1059px;
  }
  .card {
    position: absolute;
    left: 50px;
    top: 215px;
    width: 1100px;
    height: 629px;
    background: var(--card);
    border-radius: 28px;
    font-family: "Montserrat", sans-serif;
  }
  .card__frame {
    position: absolute;
    inset: 39px;
    border: 2px solid var(--ink);
  }
  .identity {
    position: absolute;
    right: 634px;
    top: 258px;
    text-align: right;
  }
  .identity__name {
    margin: 0;
    font-weight: 600;
    font-size: 47px;
    line-height: 1;
    color: var(--ink);
    letter-spacing: 0.2px;
  }
  .identity__title {
    margin: 22px 0 0;
    font-weight: 400;
    font-size: 27px;
    line-height: 1;
    color: var(--ink-soft);
    letter-spacing: 0.5px;
  }
  .divider {
    position: absolute;
    left: 520px;
    top: 258px;
    width: 3px;
    height: 110px;
    background: var(--ink);
  }
  .contact {
    position: absolute;
    left: 577px;
    top: 262px;
    margin: 0;
    padding: 0;
    list-style: none;
  }
  .contact__item {
    display: flex;
    align-items: center;
    gap: 10px;
    height: 34px;
    margin-bottom: 16px;
    font-size: 27px;
    font-weight: 400;
    color: var(--ink-soft);
    letter-spacing: 0.4px;
  }
  .contact__icon {
    width: 26px;
    height: 26px;
    flex: none;
  }
  .company {
    position: absolute;
    left: 0;
    right: 0;
    top: 500px;
    margin: 0;
    text-align: center;
    font-weight: 600;
    font-size: 22px;
    line-height: 1;
    letter-spacing: 3px;
    text-transform: uppercase;
    color: var(--ink);
  }
</style>
</head>
<body>
<div class="canvas">
  <div class="card">
    <div class="card__frame"></div>

    <div class="identity">
      <h1 class="identity__name">Delia Pratt</h1>
      <p class="identity__title">President</p>
    </div>

    <div class="divider"></div>

    <ul class="contact">
      <li class="contact__item">
        <svg class="contact__icon" viewBox="0 0 24 24" aria-hidden="true">
          <rect x="1" y="5" width="22" height="15" fill="#000"/>
          <polyline points="1.5,5.5 12,13.5 22.5,5.5" fill="none" stroke="#fff" stroke-width="1.8"/>
          <line x1="1.5" y1="19.5" x2="9.5" y2="12" stroke="#fff" stroke-width="1.5"/>
          <line x1="22.5" y1="19.5" x2="14.5" y2="12" stroke="#fff" stroke-width="1.5"/>
        </svg>
        <span>prattdq47@mailvessa.com</span>
      </li>
      <li class="contact__item">
        <svg class="contact__icon" viewBox="0 0 24 24" aria-hidden="true">
          <path d="M6.6 3.5l2.6 3.4-1.7 2.2c.9 2.4 2.8 4.3 5.2 5.3l2.2-1.7 3.4 2.6-1.6 3.2c-.4.7-1.2 1-2 .8C8.6 17.9 4.5 13.5 3.1 7.4c-.2-.8.2-1.6.9-2z" fill="#000"/>
          <path d="M13.5 6.5a4.5 4.5 0 0 1 4 4" fill="none" stroke="#000" stroke-width="1.8" stroke-linecap="round"/>
          <path d="M14 2.5a8.5 8.5 0 0 1 7.5 7.5" fill="none" stroke="#000" stroke-width="1.8" stroke-linecap="round"/>
        </svg>
        <span>703-555-0142</span>
      </li>
    </ul>

    <p class="company">TK Verdane Consulting LLC</p>
  </div>
</div>
</body>
</html>
```